Book cover design for 'Willow Reckoning' novel

Title of book 'Willow Reckoning'
Subtitle 'a Toby Fenwick novel'
Author 'R K Ashdown'
Book genre 'novel - adventure'
Format ' eBook, paperback, audio, thumbnail'
Type 'Self-publishing through PLX'
Trim size 6 x 9
Back cover 'Seeking redemption on the Senda del Brezo.
Toby Fenwick’s life changed forever in a moment of madness. Haunted by his crime, Toby feels a calling to seek redemption on the Ruta de Valdoria.
The daily toil of walking the Senda del Brezo from Seville causes Toby to search his soul.
On The Way Toby encounters other pilgrims with their own personal reasons to answer the call of the ruta.
Join Toby for the many highs and lows of ruta life as he moves step by step closer to his goal.
Can the Ruta give Toby peace of mind and stop his nightmares?'
Overall vision 'The front cover at the top should be the title:
Ruta
Calling
This will fill about 20 per cent of the front cover. It must be centre justified. The title should use the same type face as the official Ruta de Valdoria road sign (see first download). The type should be in bright blue. The background should be in bright yellow.
Under the title should be an image of a path stretching to the horizon with the shadow of a pilgrim (see second download).
Superimposed on the image should be the words 'a Toby Fenwick novel' maybe using a type face similar to the street signage used in Spain (see third download).
At the bottom of the front cover should be the author's name 'Rory Ashdown' in the same style as the blue and yellow title - BUT MUCH SMALLER.
On the SPINE of the book should be 'Willow Reckoning' and 'Rory Ashdown' in the blue text on yellow background.
On the back cover there should be a photograph (see fourth download) with the text UPDATE ON THE TEXT 'Seeking redemption on the Senda del Brezo.
In a moment of madness Toby Fenwick’s life changed forever. Haunted by his atrocious act, he feels a calling to seek redemption on the Ruta de Valdoria.
The daily slog of walking the Senda del Brezo from Seville causes Toby to search deep within his soul.
On The Way Toby encounters other pilgrims with their own personal reasons to answer the call of the Ruta.
Can the Ruta give Toby peace of mind and stop his nightmares?' with a three centimetre space at the bottom for bar code/ISBN and the author headshot photograph attached.

Target Market(s)

Readers who have walked the Ruta de Valdoria in Spain or who are interested

Requirements
Nice to have
• I would like my headshot (attached) included on the back cover

```html
<!DOCTYPE html>
<html lang="en">
<head>
<meta charset="utf-8">
<title>Willow Reckoning — Book Cover</title>
<link rel="stylesheet" href="https://fonts.googleapis.com/css2?family=Saira+Extra+Condensed:wght@600&family=Saira+Semi+Condensed:wght@400;500&display=swap">
<style>
  :root {
    --sign-yellow: #fcf000;
    --sign-blue: #1c79d2;
    --paper-white: #ffffff;
    --backdrop: #ffffff;
  }
  * { margin: 0; padding: 0; box-sizing: border-box; }
  html, body {
    width: 1200px;
    height: 1200px;
    overflow: hidden;
    background: var(--backdrop);
  }
  .cover {
    position: absolute;
    left: 263px;
    top: 95px;
    width: 674px;
    height: 1010px;
    background: var(--sign-yellow);
    overflow: hidden;
  }
  .title-sign {
    position: absolute;
    left: 39px;
    top: 40px;
    width: 596px;
    height: 557px;
    background: var(--sign-blue);
    border-radius: 34px;
  }
  .title-art {
    position: absolute;
    left: 0;
    top: 0;
    width: 596px;
    height: 557px;
  }
  .title-line {
    font-family: "Saira Extra Condensed", "Arial Narrow", sans-serif;
    font-weight: 600;
    font-size: 262px;
  }
  .title-line--upper { fill: var(--paper-white); }
  .title-line--lower { fill: var(--sign-yellow); }
  .series-line {
    position: absolute;
    left: 0;
    right: 0;
    top: 484px;
    text-align: center;
    color: var(--paper-white);
    font-family: "Saira Semi Condensed", "Arial", sans-serif;
    font-weight: 400;
    font-size: 41px;
    letter-spacing: 0.5px;
  }
  .pilgrim-shadow {
    position: absolute;
    left: 198px;
    top: 610px;
    width: 280px;
    height: 317px;
    background: radial-gradient(ellipse 30% 60% at 50% 55%, rgba(28,121,210,0.9) 0%, rgba(28,121,210,0.45) 55%, rgba(28,121,210,0) 100%);
  }
  .author-band {
    position: absolute;
    left: 0;
    bottom: 0;
    width: 100%;
    height: 83px;
    background: var(--sign-blue);
    display: flex;
    align-items: center;
    justify-content: center;
  }
  .author-name {
    color: var(--paper-white);
    font-family: "Saira Semi Condensed", "Arial", sans-serif;
    font-weight: 500;
    font-size: 54px;
    letter-spacing: 1px;
    line-height: 1;
  }
</style>
</head>
<body>
  <main class="cover">
    <section class="title-sign">
      <svg class="title-art" viewBox="0 0 596 557" role="heading" aria-level="1" aria-label="Willow Reckoning">
        <text class="title-line title-line--upper" x="298" y="226" text-anchor="middle" textLength="556" lengthAdjust="spacingAndGlyphs">WILLOW</text>
        <text class="title-line title-line--lower" x="298" y="436" text-anchor="middle" textLength="556" lengthAdjust="spacingAndGlyphs">RECKONING</text>
      </svg>
      <p class="series-line">a Toby Fenwick novel</p>
    </section>
    <div class="pilgrim-shadow" role="img" aria-label="Blue silhouette of a pilgrim's long shadow on a path, with scattered gravel specks"></div>
    <footer class="author-band">
      <p class="author-name">R K Ashdown</p>
    </footer>
  </main>
</body>
</html>
```